Skillet Sam food truck needs a flashy design for vinyl vehicle wrap.

Background: we are a new concept food truck serving high quality gourmet style burgers and burritos.

What we need:
a modern and funky design based on and using our logo and colour schemes. Black red yellow.

The background should be either yellow or white.

The vinyl wrap will cover the whole vehicle. Designs must take into account position of windows and door of the vehicle.

An accrylic logo will be positioned between the door and window on the side of vehicle. Another accrylic logo will be positioned on the other side of vehicle in the middle.

The dimensions of vehicle:
Sides: 7.3 M x 2.3 M
Front: 2.3 M x 2.3 M

Requirements
Must have
• room for the acrylic logo on the service side in between the window and door of vehicle. and on the other side preferably the middle. therefore overall design should integrate this and have a nice flow.
Nice to have
• menu items: burritos, burgers, buffalo ribs, waffles.

```html
<!DOCTYPE html>
<html lang="en">
<head>
<meta charset="UTF-8">
<title>Skillet Sam – Vehicle Wrap Side Panel</title>
<link href="https://fonts.googleapis.com/css2?family=Permanent+Marker&family=Russo+One&display=swap" rel="stylesheet">
<style>
  :root {
    --page-bg: #f2f2f2;
    --wrap-yellow: #fcc800;
    --wrap-yellow-deep: #f5b400;
    --wrap-orange: #f47a12;
    --wrap-red-orange: #d9541e;
    --band-black: #0d0d0d;
    --icon-red: #b3191c;
    --icon-ring: #f7c600;
    --ink: #111111;
    --slogan-white: #ffffff;
    --ghost-name: rgba(214, 150, 0, 0.45);
  }
  html, body {
    margin: 0;
    padding: 0;
    width: 1200px;
    height: 1000px;
    overflow: hidden;
    background: var(--page-bg);
  }
  .wrap-panel {
    position: absolute;
    left: 46px;
    top: 321px;
    width: 1108px;
    height: 357px;
    overflow: hidden;
    background: linear-gradient(180deg, var(--wrap-yellow) 0%, var(--wrap-yellow) 60%, var(--wrap-yellow-deep) 100%);
  }
  .panel-shapes {
    position: absolute;
    inset: 0;
  }
  .slogan-band {
    position: absolute;
    left: 0;
    top: 57px;
    width: 100%;
    height: 36px;
    background: var(--band-black);
  }
  .slogan {
    position: absolute;
    left: 72px;
    top: 56px;
    margin: 0;
    font-family: "Permanent Marker", cursive;
    font-size: 26px;
    line-height: 38px;
    letter-spacing: 1px;
    color: var(--slogan-white);
    white-space: nowrap;
  }
  .brand-name {
    position: absolute;
    left: 350px;
    top: 140px;
    width: 480px;
    margin: 0;
    font-family: "Russo One", sans-serif;
    font-size: 80px;
    line-height: 1;
    color: var(--ghost-name);
    white-space: nowrap;
  }
  .menu-icons {
    position: absolute;
    left: 77px;
    top: 127px;
  }
  .hero-illustration {
    position: absolute;
    left: 852px;
    top: 22px;
    width: 160px;
    height: 314px;
    border-radius: 40px 40px 60px 60px;
    background: linear-gradient(180deg, #9a9a9a 0%, #e3a04a 45%, #c98a3c 70%, #6a9a3a 82%, #e7b66a 100%);
    opacity: 0.9;
  }
</style>
</head>
<body>
  <section class="wrap-panel">
    <svg class="panel-shapes" width="1108" height="357" viewBox="0 0 1108 357" aria-hidden="true">
      <defs>
        <linearGradient id="topFade" x1="0" y1="0" x2="0" y2="1">
          <stop offset="0" stop-color="#d24a1e"/>
          <stop offset="1" stop-color="#f08a18"/>
        </linearGradient>
      </defs>
      <rect x="0" y="0" width="1108" height="60" fill="url(#topFade)"/>
      <path d="M0 270 C 150 300, 300 330, 420 357 L 0 357 Z" fill="var(--wrap-orange)"/>
      <path d="M480 357 C 700 330, 900 260, 1108 150 L 1108 357 Z" fill="var(--wrap-orange)"/>
      <path d="M600 357 C 800 335, 960 290, 1108 230 L 1108 357 Z" fill="var(--wrap-red-orange)" opacity="0.55"/>
    </svg>

    <div class="slogan-band"></div>
    <p class="slogan">"STREET FOOD IS A DISH BEST SERVED GRILLED"</p>

    <p class="brand-name">Skillet Sam</p>

    <svg class="menu-icons" width="260" height="160" viewBox="0 0 260 160" role="img" aria-label="Menu: burritos, burgers, chicken, pizza, waffles, fries">
      <g stroke="var(--ink)" stroke-width="2" fill="var(--icon-red)">
        <circle cx="38" cy="38" r="36"/><circle cx="120" cy="38" r="36"/><circle cx="204" cy="38" r="36"/>
        <circle cx="38" cy="122" r="36"/><circle cx="120" cy="122" r="36"/><circle cx="204" cy="122" r="36"/>
      </g>
      <g fill="none" stroke="var(--icon-ring)" stroke-width="2">
        <circle cx="38" cy="38" r="33"/><circle cx="120" cy="38" r="33"/><circle cx="204" cy="38" r="33"/>
        <circle cx="38" cy="122" r="33"/><circle cx="120" cy="122" r="33"/><circle cx="204" cy="122" r="33"/>
      </g>
      <g fill="none" stroke="var(--ink)" stroke-width="4" stroke-linecap="round" stroke-linejoin="round">
        <rect x="18" y="28" width="40" height="20" rx="10" transform="rotate(20 38 38)"/>
        <path d="M100 32 Q120 14 140 32 Z"/><line x1="100" y1="40" x2="140" y2="40"/><path d="M100 48 L140 48 Q140 56 120 56 Q100 56 100 48 Z"/>
        <ellipse cx="212" cy="30" rx="12" ry="10"/><line x1="204" y1="38" x2="194" y2="50"/>
        <path d="M26 104 L52 112 L34 142 Z"/>
        <circle cx="120" cy="122" r="20"/><line x1="106" y1="114" x2="134" y2="114"/><line x1="104" y1="122" x2="136" y2="122"/><line x1="106" y1="130" x2="134" y2="130"/><line x1="112" y1="104" x2="112" y2="140"/><line x1="120" y1="102" x2="120" y2="142"/><line x1="128" y1="104" x2="128" y2="140"/>
        <path d="M190 120 L218 120 L214 142 L194 142 Z"/><line x1="196" y1="120" x2="194" y2="104"/><line x1="204" y1="120" x2="204" y2="102"/><line x1="212" y1="120" x2="214" y2="104"/>
      </g>
    </svg>

    <div class="hero-illustration" role="img" aria-label="Illustration of a katana skewering a stacked burger, burrito and chicken wing"></div>
  </section>
</body>
</html>
```